We need letterhead, Business Cards, and envelops designed. We have attached a design of our logo and a sample of letterhead idea that was started but never perfected, it is only an idea for the letterhead if you can design something better we may love that also we are open to change.
We want a design that looks professional in style. we are a non profit trade association in the construction industry. the green color in the attached design represent green building, and we like that. also if you just want to enhance the letterhead sample that we attached that would be fine also.
Thanks and good luck
also the name that should show on the first business cards should be Morgan Feltwick, Director are web address is www.pvtrn.org

```html
<!DOCTYPE html>
<html lang="en">
<head>
<meta charset="utf-8">
<title>PVTRN Letterhead</title>
<link href="https://fonts.googleapis.com/css2?family=Arimo:wght@400;700&family=Raleway:wght@300&display=swap" rel="stylesheet">
<style>
  :root {
    --backdrop: #e6e6e6;
    --paper: #ffffff;
    --ink: #111111;
    --muted: #8a8a8a;
    --green: #6a9a3a;
    --rule: #222222;
  }
  * { margin: 0; padding: 0; box-sizing: border-box; }
  html, body { width: 1200px; height: 909px; overflow: hidden; background: var(--backdrop); }
  .letterhead {
    position: absolute; left: 280px; top: 40px;
    width: 640px; height: 828px;
    background: var(--paper);
    box-shadow: 0 2px 10px rgba(0,0,0,0.12);
    font-family: "Arimo", Arial, sans-serif;
    color: var(--ink);
  }
  .brand {
    position: absolute; left: 62px; top: 120px;
    display: flex; align-items: center; gap: 10px;
  }
  .brand-mark { width: 22px; height: 22px; background: var(--green); }
  .brand-name { font-weight: 700; font-size: 40px; letter-spacing: 1px; line-height: 1; }
  .brand-full {
    position: absolute; left: 62px; top: 166px;
    width: 210px; background: var(--rule); color: var(--paper);
    font-weight: 700; font-size: 8px; padding: 2px 5px; letter-spacing: 0.2px;
  }
  .contact {
    position: absolute; top: 62px; right: 56px;
    display: flex; gap: 30px;
    font-family: "Raleway", Helvetica, sans-serif; font-weight: 300;
    font-size: 9px; line-height: 1.45; color: var(--muted); letter-spacing: 0.6px;
  }
  .contact-lines li { list-style: none; display: flex; align-items: center; gap: 6px; }
  .contact-lines svg { width: 7px; height: 7px; fill: var(--green); }
  .letter {
    position: absolute; left: 122px; top: 214px; width: 460px;
    font-size: 9.6px; line-height: 1.38;
  }
  .recipient { margin-bottom: 14px; }
  .letter p { margin-bottom: 11px; }
  .signoff { margin-top: 18px; }
  .signer { margin-top: 38px; }
</style>
</head>
<body>
<main class="letterhead">
  <div class="brand">
    <span class="brand-mark"></span>
    <span class="brand-name">PVTRN</span>
  </div>
  <div class="brand-full">Pacific Valley Trades Roundtable Network</div>

  <div class="contact">
    <address class="contact-address" style="font-style:normal">address<br>4321 first street<br>anytown, State ZIP</address>
    <ul class="contact-lines">
      <li><svg viewBox="0 0 10 10"><path d="M2 1h2l1 2.5-1.3 1a6 6 0 0 0 2.8 2.8l1-1.3L10 7v2a1 1 0 0 1-1 1A9 9 0 0 1 0 1a1 1 0 0 1 1-1z"/></svg>123-456-7890</li>
      <li><svg viewBox="0 0 10 10"><rect x="1" y="2" width="8" height="6" rx="1"/></svg>123-456-7891</li>
      <li><svg viewBox="0 0 10 10"><circle cx="5" cy="5" r="4"/></svg>www.pvtrn.org</li>
    </ul>
  </div>

  <article class="letter">
    <div class="recipient">June 26, 2014<br>Trenz Pruca<br>Title<br>Company Name<br>4321 First Street<br>Anytown, State ZIP</div>
    <p>Dear Trenz,</p>
    <p>Lorem ipsum dolor sit amet, consectetur adipiscing elit, sed eiusmod tempor incidunt et labore et dolore magna aliquam. Ut enim ad minim veniam, quis nostrud exerc. Irure dolor in reprehend incididunt ut labore et dolore magna aliqua. Ut enim ad minim veniam, quis nostrud exercitation ullamco laboris nisi ut aliquip ex ea commodo consequat. Duis aute irure dolor in reprehenderit in voluptate velit esse molestaie cillum. Tia non ob ea soluad incom dereud facilis est er expedit distinct. Nam liber te conscient to factor tum poen legum odioque civiuda et tam. Neque pecun modut est neque nonor et imper ned libidig met, consectetur adipiscing elit, sed ut labore et dolore magna aliquam is nostrud exercitation ullam mmodo consequet. Duis aute in voluptate velit esse cillum dolore eu fugiat nulla pariatur.</p>
    <p>At vver eos et accusam dignissum qui blandit est praesent. Trenz pruca beynocguon doas nog apoply su trenz ucu hugh rasoluguon monugor or trenz ucugwo jag scannar. Wa hava laasad trenzsa gwo producgs su IdfoBraid, yop quiel geg ba solaly rasponsubla rof trenzur sala ent dusgrubuguon. Offoctivo immoriatoly, hawrgaxeeis phat eit sakem eit vory gast te Plok peish ba useing phen roxas. Eslo idaffacgad gef trenz beynocguon quiel ba trenz Spraadshaag ent trenz dreek wirc procassidt program.</p>
    <p>Ploaso mako nuto uf cakso dodtos anr koop a cupy uf cak vux noaw yerw phuno. Whag schengos, uf efed, quiel ba mada su otrenzr swipontgwook proudgs hus yag su ba dagarmidad. Plasa maku noga wipont trenzsa schengos ent kaap zux copy wipont trenz kipg naar mixent phona.</p>
    <p>Lorem ipsum dolor sit amet, consectetur adipiscing elit. Donec id erat quis metus suscipit mattis. Duis elit elit, venenatis id ullamcorper at, sollicitudin nec eros. Vivamus ultricies dapibus neque ut laoreet. Suspendisse massa est, fringilla quis neque a, semper consequat lacus. Etiam imperdiet dignissim nibh placerat condimentum.</p>
    <p class="signoff">Sincerely yours,</p>
    <p class="signer">Urna Semper</p>
  </article>
</main>
</body>
</html>
```